Storm Restoration Contractor needs a professional letterhead design

Looking for a professional letterhead design. Not looking for your cheapo MS Word standard ones that are readily available. Dont want it to be cookie cutter look like ones readily available online. We just recently changed our logo and want to freshen up all our documents. Our company handles restoring a property back to a pre-loss condition after a storm damages it. For example, wind, hail, flood, fire losses.

Target Market(s)

Property Owners, Homeowners, Property Owners, Commercial Property Owners, Property Management Companies

Industry/Entity Type

Construction Company

Requirements
Must have
• Professional, Use 1 of 2 logo options
• Storm Restoration, Roofing, Siding, Windows

```html
<!DOCTYPE html>
<html lang="en">
<head>
<meta charset="utf-8">
<title>Northgate Exteriors — Letterhead</title>
<link href="https://fonts.googleapis.com/css2?family=Open+Sans:wght@400;700&family=Questrial&display=swap" rel="stylesheet">
<style>
  :root {
    --bg: #e9e9ea;
    --paper: #ffffff;
    --brand-blue: #1f6fc1;
    --ink: #3a3a3a;
    --ink-dark: #222222;
    --rule-dark: #4a4a4a;
    --sig-tone: #d9d9d9;
  }
  * { box-sizing: border-box; margin: 0; padding: 0; }
  html, body {
    width: 1200px; height: 795px; overflow: hidden;
    background: var(--bg);
  }
  .canvas { position: relative; width: 1200px; height: 795px; }
  .letterhead {
    position: absolute; left: 330px; top: 16px;
    width: 540px; height: 763px;
    background: var(--paper);
    box-shadow: 0 6px 18px rgba(0,0,0,0.12);
    overflow: hidden;
    font-family: "Open Sans", sans-serif;
    color: var(--ink);
  }
  .brand {
    position: absolute; left: 44px; top: 44px;
    display: flex; align-items: center; gap: 8px;
  }
  .brand-dot {
    width: 14px; height: 14px; border-radius: 50%;
    background: var(--brand-blue);
  }
  .brand-name {
    font-family: "Questrial", sans-serif;
    font-size: 15px; letter-spacing: 1.5px;
    color: var(--brand-blue); text-transform: uppercase;
  }
  .letter-body {
    position: absolute; left: 44px; top: 150px; width: 452px;
    font-size: 9.2px; line-height: 1.45;
  }
  .salutation {
    font-weight: 700; font-size: 11px; color: var(--ink-dark);
    margin-bottom: 12px;
  }
  .letter-body p { margin-bottom: 10px; }
  .signature {
    width: 110px; height: 42px; margin-top: 22px;
    background: var(--sig-tone); border-radius: 3px;
  }
  .contact {
    position: absolute; right: 44px; bottom: 84px;
    text-align: right; font-family: "Questrial", sans-serif;
    font-size: 9.5px; line-height: 1.6; color: var(--ink-dark);
  }
  .contact-name { color: var(--brand-blue); font-size: 10px; }
  .contact-line { display: flex; justify-content: flex-end; align-items: center; gap: 3px; }
  .icon {
    width: 10px; height: 10px; border-radius: 50%;
    background: var(--brand-blue);
    display: inline-flex; align-items: center; justify-content: center;
  }
  .footer {
    position: absolute; left: 0; bottom: 0; width: 100%; height: 70px;
  }
  .footer svg { display: block; }
  .web-address {
    position: absolute; right: 50px; bottom: 34px;
    font-family: "Questrial", sans-serif; font-size: 10.5px;
    letter-spacing: 0.6px; color: var(--paper);
  }
</style>
</head>
<body>
<div class="canvas">
  <article class="letterhead">
    <header class="brand">
      <span class="brand-dot"></span>
      <span class="brand-name">Northgate Exteriors</span>
    </header>

    <section class="letter-body">
      <p class="salutation">Dear Mr. Carter,</p>
      <p>Lorem Ipsum is simply dummy text of the printing and typesetting industry. Lorem Ipsum has been the industry's standard dummy text ever since the 1500s, when an unknown printer took a galley of type and scrambled it to make a type specimen book. It has survived not only five centuries, but also the leap into electronic typesetting, remaining essentially unchanged.</p>
      <p>The standard chunk of Lorem Ipsum used since the 1500s is reproduced below for those interested. Sections 1.10.32 and 1.10.33 from "de Finibus Bonorum et Malorum" by Cicero are also reproduced in their exact original form, accompanied by English versions from the 1914 translation by H. Rackham.</p>
      <p>Lorem Ipsum is simply dummy text of the printing and typesetting industry. Lorem Ipsum has been the industry's standard dummy text ever since the 1500s, when an unknown printer took a galley of type and scrambled it to make a type specimen book. It has survived not only five centuries, but also the leap into electronic typesetting, remaining essentially unchanged. It was popularised in the</p>
      <div class="signature" role="img" aria-label="Handwritten signature"></div>
    </section>

    <address class="contact" style="font-style:normal">
      <div class="contact-name">Northgate Exteriors</div>
      <div>2280 Harbor Loop, Fairview, CA 90210</div>
      <div class="contact-line">
        <span class="icon"><svg width="6" height="6" viewBox="0 0 10 10"><path d="M2 1l2 2-1 1.5c.8 1.5 1.5 2.2 3 3L7.5 6l2 2-1.5 1.5C4 9 1 6 .5 2.5z" fill="#fff"/></svg></span>
        <span>(555) 014-2280</span>
        <span class="icon"><svg width="6" height="6" viewBox="0 0 10 10"><rect x="1" y="3" width="8" height="5" fill="#fff"/><rect x="3" y="1" width="4" height="2" fill="#fff"/></svg></span>
        <span>(555) 014-2280</span>
        <span class="icon"><svg width="6" height="6" viewBox="0 0 10 10"><rect x="1" y="2" width="8" height="6" fill="#fff"/><path d="M1 2l4 3 4-3" stroke="#1f6fc1" fill="none"/></svg></span>
        <span>info@northgateexteriors.com</span>
      </div>
    </address>

    <footer class="footer">
      <svg width="540" height="70" viewBox="0 0 540 70">
        <path d="M0 50 H290 Q300 50 306 40 L312 30 Q318 22 328 22 H540" stroke="var(--rule-dark)" stroke-width="1.2" fill="none"/>
        <path d="M0 56 H292 Q304 56 310 45 L314 37 Q320 28 332 28 H540 V70 H0 Z" fill="var(--brand-blue)"/>
      </svg>
      <span class="web-address">www.northgateexteriors.com</span>
    </footer>
  </article>
</div>
</body>
</html>
```